Automotive eCommerce Business looking for a business card design

Looking for a clean and simple business card design. Our company name is "Brindle Auto" and we are a company specializing in the ecommerce sales of automotive parts, specifically for pick up trucks and large SUVs. Our company colours are red, black, and white.

Feel free to use the logo provided or create a new logo that you seem fit. Looking forward to your creative ideas!

Industry/Entity Type

Automotive

Contact Information for Business Card

We were thinking of a possibly two-sided design featuring just the logo and company name on one side, and personal information on the other side. Single sided designs will be considered as well.

Font styles to use
Serif
Sans Serif
Decorative

Colors
ec1f27
ffffff
000000

Requirements
Must have
• Space for employee's name, title, phone number and email address, along with the company address and website somewhere.

```html
<!DOCTYPE html>
<html lang="en">
<head>
<meta charset="utf-8">
<title>Brindle Auto Ltd. – Business Card</title>
<link href="https://fonts.googleapis.com/css2?family=Cinzel:wght@500&family=Roboto:wght@400;500&display=swap" rel="stylesheet">
<style>
  :root {
    --backdrop: #2b2b2b;
    --brand-red: #9b1c20;
    --card-white: #f3f3f3;
    --steel: #535556;
    --back-grey: #4a4e4f;
    --ink-grey: #555555;
    --text-light: #ffffff;
    --mark-white: #efefef;
  }
  html, body {
    margin: 0;
    padding: 0;
    width: 1200px;
    height: 960px;
    overflow: hidden;
    background: var(--backdrop);
  }
  .canvas {
    position: relative;
    width: 1200px;
    height: 960px;
  }
  .card {
    position: absolute;
    width: 600px;
    height: 342px;
    overflow: hidden;
    box-shadow: 0 2px 6px rgba(0,0,0,.5);
  }
  .card-front { left: 314px; top: 113px; background: var(--brand-red); }
  .card-back  { left: 311px; top: 472px; background: var(--back-grey); }

  .front-panel { position: absolute; inset: 0; }

  .person {
    position: absolute;
    left: 35px;
    top: 38px;
    color: var(--text-light);
    font-family: "Roboto", sans-serif;
  }
  .person-name {
    margin: 0;
    font-size: 20px;
    font-weight: 500;
    letter-spacing: 0.2px;
  }
  .person-title {
    margin: 4px 0 0;
    font-size: 14px;
    font-weight: 500;
  }
  .address {
    position: absolute;
    left: 35px;
    top: 166px;
    margin: 0;
    color: var(--text-light);
    font: 400 14.5px/18px "Roboto", sans-serif;
    font-style: normal;
  }
  .contact-list {
    position: absolute;
    left: 35px;
    top: 212px;
    margin: 0;
    padding: 0;
    list-style: none;
    color: var(--text-light);
    font: 400 14.5px/19px "Roboto", sans-serif;
  }
  .contact-list li { display: flex; align-items: center; }
  .contact-icon { width: 14px; height: 14px; margin-right: 9px; fill: var(--text-light); }

  .brand-square {
    position: absolute;
    border-radius: 14px;
  }
  .card-front .brand-square {
    left: 369px; top: 80px; width: 122px; height: 122px;
    background: var(--brand-red);
  }
  .card-back .brand-square {
    left: 233px; top: 68px; width: 136px; height: 136px;
    background: var(--mark-white);
  }

  .brand-name {
    position: absolute;
    margin: 0;
    font-family: "Cinzel", serif;
    font-weight: 500;
    white-space: nowrap;
    transform: translateX(-50%);
  }
  .card-front .brand-name { left: 428px; top: 220px; font-size: 23.5px; color: var(--ink-grey); }
  .card-back .brand-name  { left: 300px; top: 228px; font-size: 27px; color: var(--text-light); }

  .back-web {
    position: absolute;
    left: 0;
    right: 0;
    top: 292px;
    margin: 0;
    text-align: center;
    color: var(--text-light);
    font: 400 14px "Roboto", sans-serif;
    letter-spacing: 6px;
  }
</style>
</head>
<body>
<main class="canvas">

  <section class="card card-front" aria-label="Card front">
    <svg class="front-panel" width="600" height="342" viewBox="0 0 600 342" aria-hidden="true">
      <polygon points="372,0 600,0 600,342 372,342 245,266 245,76" fill="var(--steel)"/>
      <polygon points="382,0 600,0 600,342 382,342 258,262 258,80" fill="var(--text-light)"/>
      <polygon points="386,0 600,0 600,342 386,342 262,260 262,82" fill="var(--card-white)"/>
    </svg>

    <div class="person">
      <h1 class="person-name">OWEN HARLOW</h1>
      <p class="person-title">CEO/FOUNDER</p>
    </div>

    <address class="address">2140 Alder Court<br>Fairbanks, Alaska 99701</address>

    <ul class="contact-list">
      <li><svg class="contact-icon" viewBox="0 0 24 24"><path d="M6.6 10.8a15 15 0 0 0 6.6 6.6l2.2-2.2c.3-.3.7-.4 1-.2 1.1.4 2.3.6 3.6.6.6 0 1 .4 1 1V20c0 .6-.4 1-1 1A17 17 0 0 1 3 4c0-.6.4-1 1-1h3.5c.6 0 1 .4 1 1 0 1.300.2 2.5.6 3.6.1.3 0 .7-.2 1z"/></svg>555 201 4478</li>
      <li><svg class="contact-icon" viewBox="0 0 24 24"><path d="M7 1h10a2 2 0 0 1 2 2v18a2 2 0 0 1-2 2H7a2 2 0 0 1-2-2V3a2 2 0 0 1 2-2zm0 3v14h10V4zm5 15.5a1 1 0 1 0 0 2 1 1 0 0 0 0-2z"/></svg>555 730 1926</li>
      <li><svg class="contact-icon" viewBox="0 0 24 24"><path d="M6 2h9l3 3v4H6zM3 10h18v8h-3v4H6v-4H3zm5 6v4h8v-4z"/></svg>555 864 3051</li>
      <li><svg class="contact-icon" viewBox="0 0 24 24"><path d="M2 5h20v14H2zm2 2v.5l8 5 8-5V7z"/></svg>owen@brindleauto.com</li>
      <li><svg class="contact-icon" viewBox="0 0 24 24"><path d="M12 2a10 10 0 1 0 0 20 10 10 0 0 0 0-20zm-1 17.9A8 8 0 0 1 4.2 9.2L9 14v1a2 2 0 0 0 2 2zm6.9-2.5A2 2 0 0 0 16 16h-1v-3a1 1 0 0 0-1-1H8v-2h2a1 1 0 0 0 1-1V7h2a2 2 0 0 0 2-2v-.4a8 8 0 0 1 2.9 12.8z"/></svg>www.brindleauto.com</li>
    </ul>

    <div class="brand-square" aria-hidden="true"></div>
    <p class="brand-name">Brindle Auto Ltd.</p>
  </section>

  <section class="card card-back" aria-label="Card back">
    <div class="brand-square" aria-hidden="true"></div>
    <p class="brand-name">Brindle Auto Ltd.</p>
    <p class="back-web">www.brindleauto.com</p>
  </section>

</main>
</body>
</html>
```